3 in 1 website - Property Lens Works + Keepsake Harbor LLC + Marla's Game Shots

Help me simplify and organize my business life. I am a sports photographer (action, individual and teams), real estate photographer (stills and drones) and I transfer videos and photos to jump drives, along with photo restoration, etc. Currently, I have a functioning website for the transfer/restoration business at KeepsakeHarborLLC.example which was recently created and I like it. I have received several really good ideas for the Real Estate Photography portion! I don't have anything started for the Sports Pics. My vision possibly includes a main/home page giving people the option to choose real estate, sports or transfer/restoration. I just want them combined into one site....somehow to better organize my businesses and give me ONE place to keep to updated and check for communication. I just updated the brief again and added logo files for my "parent" company called "Keepsake Harbor". I prefer this logo at the top of the main/home page, please. I previously uploaded the logo for Property Lens Works which would be used with the real estate portion of my business. At this point, I don't have a logo for the sports photography portion.

Target Market(s)

Real Estate Agents and Brokers; Sports team, parents and boosters; Community members typically 40+ years old

Industry/Entity Type

Real Estate Photography; Local sports teams; Community members 40+ years old

Coding

Coded - Design and coding required

Number of Pages Required

3 page

Requirements
Must have
• At least one page for each area: real estate, sports, digital transfers. The real estate will need to connect to an account I have with QLN for checkout options. The sports page(s) will need to connect to a 3rd party service, also. The digital transfers, photo restorations, etc. would just need a way for them to request service.
Nice to have
• I currently have a website at KeepsakeHarborLLC.example for the digital transfer/photo restoration part of my business. I like this website but want it integrated with one main site for all 3 businesses.

```html
<!DOCTYPE html>
<html lang="en">
<head>
<meta charset="utf-8">
<title>Marla Kessner – Real Estate Photographer</title>
<link href="https://fonts.googleapis.com/css2?family=Roboto:wght@400;500;700;900&family=Open+Sans:wght@700;800&display=swap" rel="stylesheet">
<style>
:root{
  --red:#e31e24;
  --blue:#1565b3;
  --sport-blue:#1a6fbf;
  --teal:#0aa096;
  --dark:#0e151d;
  --ink:#222;
  --grey:#777;
  --pale:#eef5fb;
  --white:#fff;
}
*{box-sizing:border-box;margin:0;padding:0}
html,body{width:1200px;height:4370px;overflow:hidden}
body{position:relative;font-family:'Roboto',Arial,sans-serif;color:var(--ink);background:var(--white)}
.abs{position:absolute}
.btn{position:absolute;display:flex;align-items:center;justify-content:center;gap:8px;color:var(--white);font-weight:700;font-size:14px;text-transform:uppercase;letter-spacing:.2px}
.btn .dot{width:13px;height:13px;border-radius:50%;background:var(--white);display:inline-flex;align-items:center;justify-content:center}
.btn .dot::after{content:"";border-left:5px solid currentColor;border-top:3.5px solid transparent;border-bottom:3.5px solid transparent;margin-left:1px;color:inherit}
.btn-red{background:var(--red)}
.btn-red .dot::after{border-left-color:var(--red)}
.btn-blue{background:var(--blue)}
.btn-blue .dot::after{border-left-color:var(--blue)}
.bar{position:absolute;width:38px;height:3px}

/* header */
.site-header{position:absolute;left:0;top:0;width:1200px;height:107px;background:var(--white);border-bottom:1px solid #e5e5e5}
.brand{position:absolute;left:110px;top:22px;text-align:center;width:212px}
.brand-name{font-weight:900;font-size:23px;color:var(--red);letter-spacing:-.3px;line-height:1}
.brand-tag{font-weight:500;font-size:14px;color:var(--teal);margin-top:3px}
.follow{position:absolute;left:577px;top:25px;font-size:11px;color:#555}
.social{position:absolute;top:18px;width:28px;height:28px;border-radius:50%}
.call-label{position:absolute;left:944px;top:13px;font-size:11px;color:#888}
.call-num{position:absolute;left:944px;top:31px;font-size:19px;font-weight:700;color:#222}
.vdiv{position:absolute;left:930px;top:14px;width:1px;height:42px;background:#ccc}
.main-nav{position:absolute;top:70px;left:414px;display:flex;gap:33px;font-size:15px;color:#333}
.main-nav .active{color:var(--red)}

/* hero */
.hero{position:absolute;left:0;top:107px;width:1200px;height:738px}
.hero-text{position:absolute;left:110px;color:var(--white);font-family:'Open Sans',Arial,sans-serif;text-shadow:0 2px 4px rgba(0,0,0,.45)}
.dots{position:absolute;top:725px;left:340px;display:flex;gap:4px}
.dots span{width:11px;height:11px;border-radius:50%;border:2px solid var(--white)}

/* real estate */
.sec-title{position:absolute;left:0;width:1200px;text-align:center;font-weight:900;font-size:34px;text-transform:uppercase}
.card{position:absolute;top:1022px;width:314px;height:497px;background:var(--white);border-radius:12px;box-shadow:0 0 8px rgba(0,0,0,.16)}
.card-img{position:absolute;left:5px;top:5px;width:304px;height:246px;border-radius:8px 8px 0 0}
.card h3{position:absolute;left:18px;top:274px;font-size:15px;font-weight:700}
.card p{position:absolute;left:18px;top:300px;width:278px;font-size:15px;line-height:25.5px;color:var(--grey);text-align:justify}
.card .btn{left:19px;top:422px;width:150px;height:41px}
.arrow{position:absolute;top:1253px;width:34px;height:34px;border-radius:50%;background:var(--white);box-shadow:0 0 5px rgba(0,0,0,.2)}

/* about */
.about-text{position:absolute;left:113px;top:2033px;width:478px;font-size:15px;line-height:25.7px;color:var(--grey);text-align:justify}

/* sports */
.sports{position:absolute;left:0;top:2470px;width:1200px;height:658px;background:var(--sport-blue)}
.sports-lead{position:absolute;left:200px;top:2604px;width:800px;text-align:center;color:var(--white);font-size:15px;line-height:26px}
.sport-circle{position:absolute;border-radius:50%;border:3px solid var(--white)}
.sport-label{position:absolute;top:3010px;width:260px;text-align:center;color:var(--white);font-weight:700;font-size:15px}

/* digital */
.dt-left{position:absolute;left:107px;top:3302px;width:430px;font-size:15px;line-height:25.7px;color:#555;font-weight:500;text-align:justify}
.dt-right{position:absolute;left:614px;top:3302px;width:479px;font-size:15px;line-height:25.7px;color:var(--grey);text-align:justify}

/* footer */
.foot-brand{position:absolute;left:110px;top:4030px;width:300px}
.foot-head{position:absolute;font-size:15px;font-weight:700;color:var(--white)}
.foot-head::after{content:"";position:absolute;left:0;top:24px;width:34px;height:3px;background:var(--red)}
.foot-item{position:absolute;left:502px;color:var(--white);display:flex;align-items:center;gap:16px;font-size:14px}
.foot-item .ico{width:28px;height:28px;border-radius:50%;background:var(--red);display:flex;align-items:center;justify-content:center}
.field{position:absolute;left:811px;width:275px;background:var(--white);font-size:12px;color:#777;padding:0 12px;display:flex;align-items:center;justify-content:space-between}
.foot-nav{position:absolute;left:0;top:4262px;width:1200px;display:flex;justify-content:center;gap:26px;color:var(--white);font-size:15px}
.foot-nav b{font-weight:400;color:#ccc}
.copy{position:absolute;left:0;top:4316px;width:1200px;text-align:center;color:var(--white);font-size:13px}
</style>
</head>
<body>

<header class="site-header">
  <div class="brand">
    <div class="brand-name">MARLA KESSNER</div>
    <div class="brand-tag">Real Estate Photographer</div>
  </div>
  <div class="follow">FOLLOW US:</div>
  <span class="social" style="left:661px;background:#3b5998" aria-label="Social profile"></span>
  <span class="social" style="left:697px;background:#1da1f2" aria-label="Social profile"></span>
  <span class="social" style="left:731px;background:#0e76a8" aria-label="Social profile"></span>
  <span class="social" style="left:765px;background:#d6249f" aria-label="Social profile"></span>
  <svg class="abs" style="left:824px;top:18px" width="36" height="32" viewBox="0 0 36 32" aria-label="Cart">
    <path d="M2 4h6l4 16h16l4-11H10" fill="none" stroke="#666" stroke-width="2.4" stroke-linejoin="round"/>
    <circle cx="14" cy="26" r="2.6" fill="#666"/><circle cx="26" cy="26" r="2.6" fill="#666"/>
    <circle cx="31" cy="5" r="5" fill="var(--blue)"/>
  </svg>
  <svg class="abs" style="left:892px;top:20px" width="26" height="26" viewBox="0 0 24 24" aria-label="Phone">
    <path d="M6.6 10.8a15 15 0 0 0 6.6 6.6l2.2-2.2c.3-.3.7-.4 1-.2 1.1.4 2.3.6 3.6.6.6 0 1 .4 1 1V20c0 .6-.4 1-1 1A17 17 0 0 1 3 4c0-.6.4-1 1-1h3.5c.6 0 1 .4 1 1 0 1.3.2 2.5.6 3.6.1.3 0 .7-.2 1z" fill="none" stroke="#555" stroke-width="1.6"/>
  </svg>
  <div class="vdiv"></div>
  <div class="call-label">CALL US</div>
  <div class="call-num">+1 555 010 0199</div>
  <nav class="main-nav">
    <span class="active">HOME</span><span>ABOUT US</span><span>REAL ESTATE</span><span>SPORTS</span><span>DIGITAL TRANSFERS</span><span>CONTACT US</span>
  </nav>
</header>

<section class="hero">
  <svg class="abs" style="left:0;top:0" width="1200" height="738" viewBox="0 0 1200 738">
    <defs>
      <linearGradient id="heroPhoto" x1="0" y1="0" x2="1" y2="1">
        <stop offset="0" stop-color="#6b5b4a"/><stop offset=".45" stop-color="#8a7156"/><stop offset="1" stop-color="#3a2e26"/>
      </linearGradient>
    </defs>
    <polygon points="0,0 1200,0 1200,490 348,738 0,505" fill="url(#heroPhoto)" role="img" aria-label="Photo of a furnished living and dining room interior"/>
    <polygon points="0,495 348,738 0,565" fill="var(--blue)"/>
    <polygon points="1200,490 1200,530 348,738" fill="var(--red)"/>
  </svg>
  <div class="hero-text" style="top:185px;font-size:23px;font-weight:700">WELCOME TO</div>
  <div class="hero-text" style="top:230px;font-size:48px;font-weight:800">MARLA KESSNER</div>
  <div class="hero-text" style="top:295px;font-size:37px;font-weight:700">Real Estate Photographer</div>
  <div class="btn btn-red" style="left:110px;top:368px;width:172px;height:51px">GET STARTED <span class="dot"></span></div>
  <div class="dots"><span></span><span style="background:#fff"></span><span></span></div>
</section>

<section class="real-estate">
  <div class="bar" style="left:581px;top:928px;background:var(--blue)"></div>
  <h2 class="sec-title" style="top:938px;color:var(--red)">REAL ESTATE</h2>
  <div class="arrow" style="left:35px"><svg width="34" height="34"><path d="M19 12l-5 5 5 5" fill="none" stroke="#333" stroke-width="2"/></svg></div>
  <div class="arrow" style="left:1132px"><svg width="34" height="34"><path d="M15 12l5 5-5 5" fill="none" stroke="#333" stroke-width="2"/></svg></div>

  <article class="card" style="left:107px">
    <div class="card-img" style="background:linear-gradient(160deg,#c9b9a3,#6a4a32)" role="img" aria-label="Kitchen interior with island and pendant lights"></div>
    <h3>LOREM IPSUM DOLOR SIT AMET</h3>
    <p>Lorem ipsum dolor edsited consectetur adipiscing elited sed doioef eiusmod tempor incididunt labore dolore magna veniamed quised nostrud exercitation.</p>
    <div class="btn btn-blue">VIEW MORE <span class="dot"></span></div>
  </article>
  <article class="card" style="left:445px">
    <div class="card-img" style="background:linear-gradient(180deg,#6da6dc,#c9def0 60%,#b33 100%)" role="img" aria-label="Drone flying above a bridge while a pilot watches"></div>
    <h3>LOREM IPSUM DOLOR SIT AMET</h3>
    <p>Lorem ipsum dolor edsited consectetur adipiscing elited sed doioef eiusmod tempor incididunt labore dolore magna veniamed quised nostrud exercitation.</p>
    <div class="btn btn-blue">VIEW MORE <span class="dot"></span></div>
  </article>
  <article class="card" style="left:779px">
    <div class="card-img" style="background:linear-gradient(160deg,#e6e3de,#8b8680)" role="img" aria-label="Photographer shooting a bright open kitchen"></div>
    <h3>LOREM IPSUM DOLOR SIT AMET</h3>
    <p>Lorem ipsum dolor edsited consectetur adipiscing elited sed doioef eiusmod tempor incididunt labore dolore magna veniamed quised nostrud exercitation.</p>
    <div class="btn btn-blue">VIEW MORE <span class="dot"></span></div>
  </article>

  <div class="btn btn-red" style="left:514px;top:1566px;width:173px;height:51px">VIEW MORE <span class="dot"></span></div>
</section>

<section class="about">
  <svg class="abs" style="left:0;top:1670px" width="1200" height="800" viewBox="0 0 1200 800">
    <polygon points="0,265 850,10 1200,260 1200,800 0,800" fill="var(--pale)"/>
    <polygon points="0,262 850,0 858,12 0,272" fill="var(--red)"/>
    <polygon points="850,0 1200,248 1200,262 858,12" fill="var(--teal)"/>
  </svg>
  <div class="bar" style="left:113px;top:1962px;background:var(--blue)"></div>
  <h2 class="abs" style="left:113px;top:1980px;font-size:35px;font-weight:900;color:var(--red)">ABOUT US</h2>
  <p class="about-text">Sed ut perspiciatis unde omnis iste natus error sit voluptatem accusantium doloremque laudantium, totam rem aperiam, eaque ipsa quae ab illo inventore veritatis et quasi architecto beatae vitae dicta sunt explicabo. Nemo enim ipsam voluptatem quia voluptas sit aspernatur aut odit aut fugit, sed quia consequuntur magni dolores eos qui ratione voluptatem sequi nesciunt. Neque porro quisquam est, qui dolorem ipsum quia dolor sit amet, consectetur, adipisci velit, sed quia non numquam eius modi tempora incidunt ut labore et dolore magnam aliquam quaerat voluptatem. Ut enim ad minima veniam, quis nostrum exercitationem ullam corporis suscipit laboriosam aliquid commodi consequatur. autem voluptas sit aspernatur aut ovel</p>
  <div class="btn btn-red" style="left:113px;top:2337px;width:154px;height:46px">LEARN MORE <span class="dot"></span></div>
  <svg class="abs" style="left:680px;top:1950px" width="424" height="424" viewBox="0 0 424 424">
    <defs><linearGradient id="aboutPhoto" x1="0" y1="0" x2="1" y2="1"><stop offset="0" stop-color="#b9c3cc"/><stop offset=".6" stop-color="#8a5a3c"/><stop offset="1" stop-color="#4a3a30"/></linearGradient></defs>
    <circle cx="212" cy="212" r="200" fill="url(#aboutPhoto)" role="img" aria-label="Woman in a hat holding a camera outdoors"/>
    <path d="M22 190 A192 192 0 0 1 330 60" fill="none" stroke="var(--teal)" stroke-width="5"/>
    <path d="M330 60 A192 192 0 0 1 395 270" fill="none" stroke="var(--blue)" stroke-width="5"/>
    <path d="M395 270 A192 192 0 0 1 22 190" fill="none" stroke="var(--red)" stroke-width="5"/>
  </svg>
</section>

<section class="sports">
  <div class="bar" style="left:581px;top:62px;background:var(--red)"></div>
  <h2 class="sec-title" style="top:76px;color:var(--white)">OUR SPORTS</h2>
</section>
<p class="sports-lead">Lorem ipsum dolor sit amet consectetur adipiscing elit sed do eiusmod tempor incididunt ut labore et dolore magna aliquat enim ad minim veniamquis nostrud exercitation ullamco laboris nisi ut aliquip commodo consequat.</p>
<div class="sport-circle" style="left:109px;top:2727px;width:248px;height:248px;background:linear-gradient(160deg,#c6d4e0,#3b5a2f 70%,#222)" role="img" aria-label="Camera operator filming a match on a sports field"></div>
<div class="sport-circle" style="left:633px;top:2727px;width:248px;height:248px;background:linear-gradient(160deg,#d9d2c8,#54463c 60%,#1c1c1c)" role="img" aria-label="Photographer aiming a camera"></div>
<div class="sport-circle" style="left:869px;top:2727px;width:248px;height:248px;background:linear-gradient(160deg,#e2d8c4,#b58d58 60%,#3a5a8a)" role="img" aria-label="Camera on tripod in an indoor gym"></div>
<div class="sport-circle" style="left:340px;top:2695px;width:312px;height:312px;border:7px solid var(--teal);background:linear-gradient(160deg,#2a3340,#3d6a2c 70%,#1c2a14)" role="img" aria-label="Photographer with a telephoto lens at a football match">
  <div style="position:absolute;left:0;top:122px;width:298px;text-align:center;color:#fff;font-size:20px;font-weight:500;line-height:26px">Lorem ipsum<br>dolor sit</div>
</div>
<div class="sport-label" style="left:103px">Lorem ipsum dolor sit</div>
<div class="sport-label" style="left:627px">Lorem ipsum dolor sit</div>
<div class="sport-label" style="left:863px">Lorem ipsum dolor sit</div>

<section class="digital">
  <div class="bar" style="left:581px;top:3210px;background:var(--blue)"></div>
  <h2 class="sec-title" style="top:3229px"><span style="color:var(--red)">DIGITAL</span> <span style="color:var(--teal)">TRANSFERS</span></h2>
  <p class="dt-left">Sed ut perspiciatis unde omnis iste natus error sit voluptatem accusantium doloremque laudantium, totam rem aperiam, eaque ipsa quae ab illo inventore veritatis et quasi .</p>
  <div class="abs" style="left:107px;top:3394px;width:443px;height:276px;border:4px solid #ddd;box-shadow:0 2px 6px rgba(0,0,0,.35);background:linear-gradient(150deg,#d8d8d8,#6d6d6d 55%,#2b2b2b)" role="img" aria-label="Vintage folding camera resting on old printed photos"></div>
  <p class="dt-right">Sed ut perspiciatis unde omnis iste natus error sit voluptatem accusantium doloremque laudantium, totam rem aperiam, eaque ipsa quae ab illo inventore veritatis et quasi architecto beatae vitae dicta sunt explicabo. Nemo enim ipsam voluptatem quia voluptas sit aspernatur aut odit aut fugit, sed quia consequuntur magni dolores eos qui ratione voluptatem sequi nesciunt. Neque porro quisquam est, qui dolorem ipsum quia dolor sit amet, consectetur, adipisci velit, sed quia non numquam eius modi tempora incidunt ut labore et dolore magnam aliquam quaerat voluptatem. Ut enim ad minima veniam, quis nostrum exercitationem ullam corporis suscipit laboriosam aliquid commodi consequatur. autem voluptas sit aspernatur aut ovel</p>
  <div class="btn btn-red" style="left:614px;top:3655px;width:155px;height:46px">LEARN MORE <span class="dot"></span></div>
</section>

<footer class="site-footer">
  <svg class="abs" style="left:0;top:3740px" width="1200" height="630" viewBox="0 0 1200 630">
    <polygon points="0,240 858,6 1200,200 1200,630 0,630" fill="var(--dark)"/>
    <polygon points="0,228 858,0 862,14 0,262" fill="var(--red)"/>
    <polygon points="858,0 1200,188 1200,228 862,14" fill="var(--teal)"/>
  </svg>
  <div class="foot-brand">
    <div style="font-weight:900;font-size:31px;color:var(--red);letter-spacing:-.3px">MARLA KESSNER</div>
    <div style="font-weight:500;font-size:19px;color:var(--teal);margin-top:2px">Real Estate Photographer</div>
  </div>
  <div class="abs" style="left:112px;top:4110px;color:#fff;font-size:17px;font-weight:500">Follow Us On</div>
  <div class="abs" style="left:112px;top:4135px;width:34px;height:3px;background:var(--red)"></div>
  <span class="abs" style="left:110px;top:4153px;width:34px;height:34px;border-radius:50%;border:1.5px solid #fff" aria-label="Social profile"></span>
  <span class="abs" style="left:151px;top:4153px;width:34px;height:34px;border-radius:50%;border:1.5px solid #fff" aria-label="Social profile"></span>

  <div class="foot-head" style="left:489px;top:3956px">ADDRESS</div>
  <div class="foot-item" style="top:4012px;font-weight:500">
    <span class="ico"><svg width="12" height="16" viewBox="0 0 12 16"><path d="M6 0a6 6 0 0 0-6 6c0 4.5 6 10 6 10s6-5.5 6-10a6 6 0 0 0-6-6zm0 8.3A2.3 2.3 0 1 1 6 3.7a2.3 2.3 0 0 1 0 4.6z" fill="#fff"/></svg></span>153,Lorem ipsum dolor sit</div>
  <div class="foot-item" style="top:4075px;font-size:19px;font-weight:700">
    <span class="ico"><svg width="14" height="14" viewBox="0 0 24 24"><path d="M6.6 10.8a15 15 0 0 0 6.6 6.6l2.2-2.2c.3-.3.7-.4 1-.2 1.1.4 2.3.6 3.6.6.6 0 1 .4 1 1V20c0 .6-.4 1-1 1A17 17 0 0 1 3 4c0-.6.4-1 1-1h3.5c.6 0 1 .4 1 1 0 1.3.2 2.5.6 3.6.1.3 0 .7-.2 1z" fill="#fff"/></svg></span>+ 1 555 010 0199</div>
  <div class="foot-item" style="top:4132px">
    <span class="ico"><svg width="14" height="11" viewBox="0 0 14 11"><rect x="0" y="0" width="14" height="11" rx="1.5" fill="#fff"/><path d="M0.5 1l6.5 5 6.5-5" fill="none" stroke="var(--red)" stroke-width="1.4"/></svg></span>info@propertylensworks.example</div>

  <div class="foot-head" style="left:811px;top:3956px">GET IN TOUCH</div>
  <div class="field" style="top:4010px;height:42px">Email Address *<svg width="13" height="10" viewBox="0 0 14 11"><rect width="14" height="11" rx="1.5" fill="#777"/><path d="M0.5 1l6.5 5 6.5-5" fill="none" stroke="#fff" stroke-width="1.3"/></svg></div>
  <div class="field" style="top:4067px;height:41px">Email Name *<svg width="10" height="12" viewBox="0 0 10 12"><circle cx="5" cy="3" r="3" fill="#777"/><path d="M0 12a5 5 0 0 1 10 0z" fill="#777"/></svg></div>
  <div class="btn btn-blue" style="left:811px;top:4122px;width:275px;height:44px;font-size:15px">SUBMIT NOW <span class="dot"></span></div>

  <div class="abs" style="left:110px;top:4234px;width:980px;height:1px;background:#3a434d"></div>
  <nav class="foot-nav">
    <span style="font-weight:700">HOME</span><b>|</b><span>ABOUT US</span><b>|</b><span>REAL ESTATE</span><b>|</b><span>SPORTS</span><b>|</b><span>DIGITAL TRANSFERS</span><b>|</b><span>CONTACT US</span>
  </nav>
  <div class="copy">© 2023 Marla Kessner - Real Estate Photographer. All Rights Reserved</div>
</footer>

</body>
</html>
```